Allied Health team of Physiotherapists & Occupational Therapists seek a business card design

We have our new logo, we now need our new business cards and stationary. Tidewell: Oedema & Family Clinic is seeking a generic card design to represent our whole team and individual cards for each therapist that incorporates our new logo to communicate our holistic approach that is calming, nuturing, supportive and welcoming.
Our Physiotherapists and Occupational Therapists assess, treat and provide education for people who are at risk of or who have lymphoedema. This is often as a result of treatment for cancer. We provide pre-operative and post-operative management and cancer rehabilitation in our Pilates studio. Our team also consists of Physiotherapists who have a strong interest in pelvic floor and continence management for both men and women.

Target Market(s)

Mainly women health conscious

Industry/Entity Type

Allied Health: Physiotherapy / Occupational Therapy

Contact Information for Business Card

Address: 14 Gallivant Ave Frankston 3199 Phone: 84316570 fax: 8431 6578 Email: info@tidewellcareservices.com.au Website: tidewellcareservices.com.au Facebook address: facebook.com/TidewellOedemaAndFamilyCareClinic. Room to write appointments. Individual cards need to have name, office email and individual email and professional details

Requirements
Must have
• Logo as per uploaded documents

```html
<!DOCTYPE html>
<html lang="en">
<head>
<meta charset="utf-8">
<title>Tidewell: Oedema &amp; Family Clinic — Business Card</title>
<link rel="stylesheet" href="https://fonts.googleapis.com/css2?family=Libre+Baskerville:wght@700&family=Open+Sans:wght@400;600&display=swap">
<style>
  :root {
    --stage: #c9c9c9;
    --paper: #ffffff;
    --peach: #f8b185;
    --sage: #c5cdc1;
    --ink-white: #ffffff;
  }
  * { box-sizing: border-box; margin: 0; padding: 0; }
  html, body { width: 1200px; height: 1035px; overflow: hidden; }
  body {
    background: var(--stage);
    font-family: "Open Sans", sans-serif;
    position: relative;
  }
  .card {
    position: absolute;
    width: 620px;
    height: 354px;
    overflow: hidden;
    box-shadow: 0 10px 28px rgba(0,0,0,0.18);
  }
  .card-front { left: 70px; top: 90px; background: var(--paper); }
  .card-back { left: 510px; top: 580px; background: var(--peach); }

  .front-shapes { position: absolute; inset: 0; }

  .brand-name {
    position: absolute;
    left: 0; right: 0;
    text-align: center;
    font-family: "Open Sans", sans-serif;
    font-weight: 600;
    letter-spacing: 0.12em;
    text-transform: uppercase;
    line-height: 1.5;
  }
  .card-front .brand-name {
    top: 52px;
    font-size: 15px;
    color: var(--peach);
  }
  .card-back .brand-name {
    top: 120px;
    font-size: 22px;
    color: var(--ink-white);
  }

  .person {
    position: absolute;
    left: 42px;
    top: 170px;
    color: var(--ink-white);
  }
  .person-name {
    font-family: "Libre Baskerville", serif;
    font-weight: 700;
    font-size: 17px;
    letter-spacing: 0.04em;
  }
  .person-role {
    font-size: 9.5px;
    margin-top: 1px;
  }

  .contact-list {
    position: absolute;
    left: 42px;
    top: 226px;
    list-style: none;
    color: var(--ink-white);
    font-size: 12.5px;
  }
  .contact-item {
    display: flex;
    align-items: center;
    gap: 10px;
    margin-bottom: 9px;
  }
  .contact-item .gap { display: inline-block; width: 22px; }
  .icon {
    width: 20px; height: 20px;
    flex: none;
  }
  .inline-icon { display: inline-flex; align-items: center; gap: 10px; }

  .website {
    position: absolute;
    right: 44px;
    bottom: 50px;
    color: var(--ink-white);
    font-size: 19px;
    letter-spacing: 0.28em;
  }
</style>
</head>
<body>

<section class="card card-front" aria-label="Card front">
  <svg class="front-shapes" width="620" height="354" viewBox="0 0 620 354" aria-hidden="true">
    <polygon points="0,160 300,160 345,208 0,208" fill="var(--sage)"/>
    <polygon points="0,208 345,208 390,160 620,160 620,354 0,354" fill="var(--peach)"/>
  </svg>

  <p class="brand-name">Tidewell: Oedema<br>&amp; Family Clinic</p>

  <div class="person">
    <p class="person-name">MARA ELLISON</p>
    <p class="person-role">CEO/Managing Director</p>
  </div>

  <ul class="contact-list">
    <li class="contact-item">
      <svg class="icon" viewBox="0 0 20 20" aria-hidden="true">
        <rect width="20" height="20" rx="4" fill="var(--ink-white)"/>
        <path d="M6.5 4.5l2 2.3-1.2 1.6c.8 1.6 2 2.8 3.6 3.6l1.6-1.2 2.3 2-1 1.8c-4.6-.2-8.4-4-8.6-8.6z" fill="var(--peach)"/>
      </svg>
      <span>310-555-0147</span>
      <span class="gap"></span>
      <span class="inline-icon">
        <svg class="icon" viewBox="0 0 20 20" aria-hidden="true">
          <rect width="20" height="20" rx="4" fill="var(--ink-white)"/>
          <rect x="6" y="4" width="8" height="4" fill="var(--peach)"/>
          <rect x="4" y="8" width="12" height="6" rx="1" fill="var(--peach)"/>
          <rect x="6" y="12" width="8" height="4" fill="var(--ink-white)" stroke="var(--peach)" stroke-width="1"/>
        </svg>
        <span>310-555-0147</span>
      </span>
    </li>
    <li class="contact-item">
      <svg class="icon" viewBox="0 0 20 20" aria-hidden="true">
        <rect width="20" height="20" rx="4" fill="var(--ink-white)"/>
        <rect x="4" y="6" width="12" height="8" fill="none" stroke="var(--peach)" stroke-width="1.4"/>
        <path d="M4 6l6 5 6-5" fill="none" stroke="var(--peach)" stroke-width="1.4"/>
      </svg>
      <span>maraellison@tidewellmail.com</span>
    </li>
    <li class="contact-item">
      <svg class="icon" viewBox="0 0 20 20" aria-hidden="true">
        <rect width="20" height="20" rx="4" fill="var(--ink-white)"/>
        <path d="M10 4a4 4 0 0 1 4 4c0 3-4 8-4 8s-4-5-4-8a4 4 0 0 1 4-4z" fill="var(--peach)"/>
        <circle cx="10" cy="8" r="1.5" fill="var(--ink-white)"/>
      </svg>
      <span>88 Harlow Street NW Suite 210 Lakemont MI 49021</span>
    </li>
  </ul>
</section>

<section class="card card-back" aria-label="Card back">
  <p class="brand-name">Tidewell: Oedema<br>&amp; Family Clinic</p>
  <p class="website">www.tidewellcare.com</p>
</section>

</body>
</html>
```